Hi,
We are also sourcing for a logo, if you have ideas please take a look at our other project (if you look at our profile you should be able to see it).
We are looking for a website that will be used to manage mobile devices. The feature set is rather small, users can Wipe, Lock, Locate devices as well as make them Ring or Speak (by sending text to be spoken). We attached some images of what it looks like right now. We are looking for simplicity, uniformity and most importantly, the website should be thought of as primary User Interface, it should flow.
Please see attached to get an idea of what it looks like now. The current design was inspired by making a site that will work and flow well on a variety of displays (from mobile to tablet to desktop).
We want to stay away from radio buttons, check-boxes. This should be engaging and creative, opposite of Corporate. Not busy (ideally we are looking to have fewest possible choices at any given time and at the same time no feature should be more than 3 clicks away (this is a suggestion/approximation... just want to share our understanding of what 'flow' is).
Could be cartoony.
Thanks!
BrisketLoom
Reason: there are a couple of designs that are interesting, in addition to specific feedback I provided, possibly looking for more concepts.
Thank You

```html
<!DOCTYPE html>
<html lang="en">
<head>
<meta charset="utf-8">
<title>BrisketLoom – Lost UR Phone?</title>
<link rel="stylesheet" href="https://fonts.googleapis.com/css2?family=Alfa+Slab+One&family=Allerta+Stencil&family=Architects+Daughter&family=Graduate&family=Varela+Round&display=swap">
<style>
  :root {
    --page-bg: #e4e4e4;
    --night: #131820;
    --night-mid: #1d2838;
    --glow-soft: rgba(90, 170, 240, 0.45);
    --sky: #8cc8ef;
    --sky-deep: #4f9bd6;
    --ink: #101418;
    --chalk: #f4f2ea;
  }
  * { box-sizing: border-box; margin: 0; padding: 0; }
  html, body { width: 1200px; height: 848px; overflow: hidden; }
  body { background: var(--page-bg); position: relative; }

  .landing {
    position: absolute; left: 112px; top: 10px; width: 976px; height: 828px;
    overflow: hidden;
    background:
      radial-gradient(ellipse 14% 70% at 52% 48%, var(--glow-soft), transparent 70%),
      radial-gradient(circle at 30% 78%, rgba(120,190,245,0.35), transparent 22%),
      radial-gradient(circle at 85% 20%, rgba(70,120,180,0.3), transparent 35%),
      linear-gradient(160deg, var(--night-mid), var(--night) 60%, #0c1016);
  }
  .light-beam {
    position: absolute; left: 470px; top: 0; width: 40px; height: 828px;
    background: linear-gradient(90deg, transparent, rgba(150,210,255,0.45), transparent);
  }
  .orbits { position: absolute; inset: 0; }

  .brand {
    position: absolute; left: 692px; top: 43px; width: 228px; height: 41px;
    background: var(--sky); color: var(--ink);
    font: 26px/41px "Varela Round", sans-serif; text-align: center;
    white-space: nowrap;
  }

  .headline { position: absolute; inset: 0; pointer-events: none; font-weight: 400; }
  .headline span {
    position: absolute; background: var(--sky); color: var(--ink);
    font-family: "Allerta Stencil", sans-serif; text-align: center;
    box-shadow: 3px 4px 0 rgba(0,0,0,0.5); white-space: nowrap;
  }
  .headline .word-lost  { left: 128px; top: 108px; width: 192px; height: 78px; font-size: 62px; line-height: 78px; transform: rotate(-2deg); }
  .headline .word-ur    { left: 332px; top: 96px;  width: 96px;  height: 84px; font-size: 58px; line-height: 84px; transform: rotate(3deg); }
  .headline .word-phone { left: 442px; top: 116px; width: 304px; height: 86px; font-size: 62px; line-height: 86px; transform: rotate(-1deg); }

  .main-nav a {
    position: absolute; left: 36px; width: 232px; display: block;
    background: linear-gradient(90deg, var(--sky-deep), var(--sky));
    clip-path: polygon(0 0, 100% 0, 92% 100%, 6% 100%);
    color: var(--ink); text-decoration: none; text-align: center;
    font: 20px "Graduate", serif; white-space: nowrap;
  }
  .main-nav .nav-home     { top: 333px; height: 65px; line-height: 65px; }
  .main-nav .nav-services { top: 435px; height: 72px; line-height: 72px; }
  .main-nav .nav-contact  { top: 539px; height: 70px; line-height: 70px; }

  .device-art {
    position: absolute; left: 340px; top: 225px; width: 266px; height: 405px;
    border-radius: 22px;
    background: linear-gradient(150deg, var(--sky) 0%, #1c2a3a 45%, var(--sky-deep) 100%);
  }

  .actions {
    position: absolute; left: 606px; top: 284px;
    color: var(--chalk); font: 56px/64px "Alfa Slab One", serif;
    transform: rotate(-3deg); white-space: nowrap;
  }
  .find-it {
    position: absolute; left: 512px; top: 606px;
    color: var(--chalk); font: 56px/70px "Alfa Slab One", serif; white-space: nowrap;
  }
  .get-app {
    position: absolute; left: 522px; top: 686px; width: 288px; height: 84px;
    background: var(--sky); color: var(--ink); text-decoration: none;
    font: 38px/84px "Architects Daughter", cursive; text-align: center;
    transform: rotate(-1deg); white-space: nowrap;
  }
</style>
</head>
<body>
<main class="landing">
  <div class="light-beam"></div>

  <svg class="orbits" width="976" height="828" viewBox="0 0 976 828" fill="none" stroke="#e9eef3">
    <circle cx="976" cy="0" r="240" stroke-width="3"/>
    <circle cx="630" cy="440" r="100" stroke-width="2"/>
    <path d="M0 190 Q300 150 520 230" stroke-width="2" opacity="0.6"/>
    <circle cx="620" cy="410" r="44" fill="#6fb3e6" stroke="none" opacity="0.8"/>
    <circle cx="260" cy="670" r="44" fill="#f2f2f2" stroke="none" opacity="0.7"/>
    <circle cx="260" cy="780" r="52" fill="#5aa6e0" stroke="none" opacity="0.7"/>
    <circle cx="880" cy="100" r="14" fill="#cfd6dd" stroke="none"/>
    <circle cx="800" cy="810" r="12" stroke-width="2"/>
    <circle cx="560" cy="460" r="120" stroke-width="1" opacity="0.4"/>
  </svg>

  <div class="brand">BrisketLoom</div>

  <h1 class="headline" aria-label="Lost UR phone?">
    <span class="word-lost">LOST</span>
    <span class="word-ur">UR</span>
    <span class="word-phone">PHONE?</span>
  </h1>

  <nav class="main-nav">
    <a class="nav-home" href="#">HOME</a>
    <a class="nav-services" href="#">SERVICES</a>
    <a class="nav-contact" href="#">CONTACT US</a>
  </nav>

  <div class="device-art" role="img" aria-label="Illustration of a tablet showing a padlock and a phone with an app grid"></div>

  <p class="actions">LOCK IT!<br>RING IT!<br>WIPE IT!</p>
  <p class="find-it">FIND IT!</p>
  <a class="get-app" href="#">GET THE APP</a>
</main>
</body>
</html>
```